Bright Net Rally Website Design (design layout only)

We need a website design for a new nonprofit organization based in Des Moines, Iowa called Bright Net Rally. The nonprofit provides soccer training opportunities to youth soccer players looking to improve their game while also affecting the lives of the less fortunate in a positive way. While participating in the training programs the players also go out and raise money for selected charities. The organization then donates the funds. In its first 18 months we donated $10,500. We would like to see designs attempt to symbolize the mission of the nonprofit - essentially "improve you while improving someone else."

We would like to see the following features:

· A place to donate - Our intent is to have the home page linked to the donation page; a simple straight-forward process for people to give money, and make donating as painless as possible - no account needed to make a donation, credit card or e-check should be the only information needed to donate, and have it be on a single page.

· A photo gallery so people can browse the photo gallery to get a better understanding of our organization and a place to add videos and a calendar to show upcoming events

· A place for contact information and the profiles of directors and board members. This should include a spot showing all the charities the organization donates to. Also includes a news section/blog for comments and suggestions.

We want the design to revolve around the content and mission. We would really like to stress our organization as nonprofit. We would also like if the website was user friendly and easy to navigate.

The logo of our organization is uploaded

```html
<!DOCTYPE html>
<html lang="en">
<head>
<meta charset="utf-8">
<title>Bright Net Rally</title>
<link href="https://fonts.googleapis.com/css2?family=Oswald:wght@300;400;500;700&family=Roboto:wght@400;500&display=swap" rel="stylesheet">
<style>
:root{
  --green:#6f9a48;
  --green-dark:#4f7a34;
  --green-soft:#8fae72;
  --blue:#1c64c4;
  --blue-dark:#0d3f90;
  --ink:#333;
  --muted:#888;
  --line:#c9d8b8;
  --panel:#ffffff;
  --footer:#9a9a9a;
  --black:#0c0c0c;
}
*{margin:0;padding:0;box-sizing:border-box}
html,body{width:752px;height:1200px;overflow:hidden}
body{position:relative;background:#fff;font-family:Roboto,Arial,sans-serif;color:var(--ink)}
.abs{position:absolute}
.site-header{left:0;top:0;width:752px;height:38px;background:linear-gradient(#fff,#ececec);z-index:3}
.brand{left:106px;top:10px;font:700 15px/1 Oswald,sans-serif;color:var(--green);letter-spacing:.3px;display:flex;align-items:center;gap:5px;white-space:nowrap}
.brand i{width:9px;height:9px;border-radius:50%;background:var(--green);display:block}
.nav{left:296px;top:0;height:38px;display:flex;align-items:center;gap:19px;font:400 8.4px Oswald,sans-serif;color:#555;text-transform:uppercase}
.nav-donate{left:583px;top:0;width:67px;height:38px;background:var(--green);color:#fff;font:500 8.6px Oswald,sans-serif;display:flex;align-items:center;justify-content:center;gap:5px}
.search{left:657px;top:11px}
.hero{left:0;top:38px;width:752px;height:306px;background:linear-gradient(180deg,#1b1f1d 0%,#232a24 45%,#2f5a22 75%,#3f7a2a 100%)}
.hero-title{left:106px;top:88px;font:700 40px/1 Oswald,sans-serif;color:#fff;letter-spacing:-1px;white-space:nowrap;z-index:1}
.hero-title span{font-weight:300}
.hero-sub{left:106px;top:132px;width:312px;text-align:right;font:500 27px/1 Oswald,sans-serif;color:#fff;letter-spacing:-.5px;white-space:nowrap;z-index:1}
.panel{left:106px;top:274px;width:575px;height:180px;background:var(--panel);border-top:8px solid var(--green-soft);box-shadow:0 4px 12px rgba(0,0,0,.15)}
.sec-title{font:300 14px/1 Oswald,sans-serif;color:#555;display:flex;align-items:center;gap:5px;padding-bottom:4px;border-bottom:2px solid var(--line);width:104px;white-space:nowrap}
.sec-title b{width:13px;height:13px;border-radius:50%;border:2px solid var(--green-dark);background:#fff;display:block;flex:none}
.thumb{width:127px;height:70px;border:3px solid #eee;box-shadow:0 1px 3px rgba(0,0,0,.3)}
.caption{width:127px;font-size:6px;line-height:1.45;color:#666;text-align:center}
.donate-bar{left:106px;top:454px;width:575px;height:69px;background:linear-gradient(90deg,#1656b0,#2a7ad6 55%,#1656b0)}
.goal{top:0;width:105px;height:69px;background:var(--blue-dark);color:#fff;text-align:center;font:300 12px Oswald,sans-serif;padding-top:16px}
.goal strong{display:block;font:700 18px/1.2 Oswald,sans-serif}
.give{left:134px;top:14px;color:#fff;font:300 10px/1 Oswald,sans-serif;white-space:nowrap}
.give strong{display:block;font:700 17px/1.3 Oswald,sans-serif;letter-spacing:-.3px}
.give-text{left:210px;top:28px;width:132px;color:#fff;font-size:6.2px;line-height:1.45}
.donate-btn{left:356px;top:24px;width:98px;height:21px;background:#fff;color:var(--blue-dark);font:500 10.5px/21px Oswald,sans-serif;text-align:center}
.member{width:100px;text-align:center}
.avatar{width:72px;height:72px;border-radius:50%;margin:0 auto;background:radial-gradient(circle at 50% 40%,#6e8aa0,#24384c);box-shadow:0 2px 4px rgba(0,0,0,.3)}
.member h4{font:400 10.5px/1 Oswald,sans-serif;color:#333;margin-top:14px}
.member p{font-size:6.6px;color:#555;margin-top:5px}
.news-item{left:120px;width:187px;height:50px}
.date{left:0;top:0;width:33px;height:33px;border-radius:50%;background:var(--green-dark);color:#fff;text-align:center;font:400 13px/1 Oswald,sans-serif;padding-top:4px;box-shadow:0 0 0 2px #dfe8d4}
.date small{display:block;font-size:7px}
.news-text{left:42px;top:0;width:145px}
.news-text h5{font:500 7.6px Roboto,sans-serif;color:var(--green)}
.news-text p{font-size:5.8px;line-height:1.45;color:#999;margin-top:2px}
.rule{height:1px;background:#ddd;left:160px;width:147px}
.blog-img{left:342px;width:131px;height:51px;border-radius:3px}
.blog-cap{left:342px;width:131px;font-size:5.8px;line-height:1.45;color:#888}
.events{left:520px;top:786px;width:138px;height:179px;border:1px solid #d6d6d6;background:linear-gradient(#f4f4f4,#e3e3e3);text-align:center;padding-top:18px}
.events h3{font:500 16px/1 Oswald,sans-serif;color:var(--green)}
.events p{font:300 10px/1.6 Oswald,sans-serif;color:var(--green-soft);margin-top:6px}
.partners{left:106px;top:993px;width:575px;height:57px;background:var(--black);display:flex;align-items:center}
.partners h3{font:400 15px Oswald,sans-serif;color:var(--green-soft);margin-left:16px;padding-right:10px;border-right:2px solid var(--green-soft);height:38px;line-height:38px;border-radius:0 12px 12px 0}
.partner-list{display:flex;gap:26px;margin-left:30px;font:500 11px Oswald,sans-serif;color:#777}
.stripe{left:0;top:1070px;width:752px;height:4px;background:repeating-linear-gradient(90deg,var(--green-soft) 0 3px,transparent 3px 5px)}
.footer{left:0;top:1078px;width:752px;height:122px;background:var(--footer);color:#fff}
.foot-brand{left:106px;top:26px;font:700 20px/1 Oswald,sans-serif;color:#fff;display:flex;align-items:center;gap:7px;white-space:nowrap}
.foot-brand i{width:13px;height:13px;border-radius:50%;background:#fff;display:block}
.socials{left:106px;top:81px;display:flex;gap:8px;align-items:center}
.socials i{width:15px;height:15px;border-radius:50%;border:1.5px solid #fff;display:block}
.socials span{font:400 6.6px Oswald,sans-serif;margin-left:10px}
.foot-text{left:294px;top:16px;width:210px;font-size:6.3px;line-height:1.45}
.foot-col{top:18px;font-size:6.2px;line-height:2.1}
.foot-col h4{font:400 8.6px/1.4 Oswald,sans-serif;margin-bottom:2px}
</style>
</head>
<body>

<header class="abs site-header">
  <div class="abs brand"><i></i>BRIGHT NET RALLY</div>
  <nav class="abs nav"><span>Home</span><span>News</span><span>Fixtures</span><span>Results</span><span>Gallery</span><span>Blog</span><span>Contact</span></nav>
  <div class="abs nav-donate">
    <svg width="11" height="10" viewBox="0 0 11 10"><path d="M1 7h3l2 1 4-2v2l-4 2-5-1z" fill="#fff"/><circle cx="6.5" cy="3" r="2" fill="#fff"/></svg>DONATE</div>
  <svg class="abs search" width="15" height="15" viewBox="0 0 15 15"><circle cx="6" cy="6" r="4.5" fill="none" stroke="#666" stroke-width="1.6"/><path d="M9.5 9.5l4 4" stroke="#666" stroke-width="1.8"/></svg>
</header>

<section class="abs hero" role="img" aria-label="Player's boots and a soccer ball beside orange training cones on a floodlit pitch"></section>
<h1 class="abs hero-title">IMPROVE YOU <span>WHILE</span></h1>
<div class="abs hero-sub">SOME ELSE IMPROVING</div>

<section class="abs panel">
  <h2 class="abs sec-title" style="left:18px;top:21px"><b></b>GALLERY</h2>
  <div class="abs thumb" style="left:20px;top:46px;background:linear-gradient(#0c1830,#1a2b50)" role="img" aria-label="Players training on a dark indoor pitch"></div>
  <div class="abs thumb" style="left:156px;top:46px;background:linear-gradient(#4a3a30,#8a6a50)" role="img" aria-label="Players challenging for the ball in a match"></div>
  <div class="abs thumb" style="left:292px;top:46px;background:linear-gradient(#3e6a30,#a04a20)" role="img" aria-label="Team huddled together on the pitch"></div>
  <div class="abs thumb" style="left:428px;top:46px;background:linear-gradient(#9ab3c8,#5a8a40)" role="img" aria-label="Youth players on a training field by a goal"></div>
  <p class="abs caption" style="left:20px;top:130px">Lorem ipsum dolor sit amet, consectetuer adipiscing elit, sed diam nonummy dolore magna aliquam erat volutpat.</p>
  <p class="abs caption" style="left:156px;top:130px">Lorem ipsum dolor sit amet, consectetuer adipiscing elit, sed diam nonummy dolore magna aliquam erat volutpat.</p>
  <p class="abs caption" style="left:292px;top:130px">Lorem ipsum dolor sit amet, consectetuer adipiscing elit, sed diam nonummy dolore magna aliquam erat volutpat.</p>
  <p class="abs caption" style="left:428px;top:130px">Lorem ipsum dolor sit amet, consectetuer adipiscing elit, sed diam nonummy dolore magna aliquam erat volutpat.</p>
</section>

<section class="abs donate-bar">
  <div class="abs goal" style="left:0">Our Goal<strong>$20,000</strong></div>
  <div class="abs give">Give Us<strong>DONATION</strong></div>
  <p class="abs give-text">Lorem ipsum dolor sit amet, consetuer adipiscing elit, sed diammy dolore magna aliquam erat volutpat.</p>
  <div class="abs donate-btn">DONATE NOW!</div>
  <div class="abs goal" style="left:470px">More Needed<strong>$10,000</strong></div>
</section>

<h2 class="abs sec-title" style="left:124px;top:563px"><b></b>OUR TEAM</h2>
<div class="abs member" style="left:134px;top:596px"><div class="avatar" role="img" aria-label="Portrait of Dale Brennan"></div><h4>Dale Brennan</h4><p>CEO</p></div>
<div class="abs member" style="left:231px;top:596px"><div class="avatar" role="img" aria-label="Portrait of Shana Jessup"></div><h4>Shana Jessup</h4><p>Manager</p></div>
<div class="abs member" style="left:324px;top:596px"><div class="avatar" role="img" aria-label="Portrait of Miles Blake"></div><h4>Miles Blake</h4><p>Accountant</p></div>
<div class="abs member" style="left:416px;top:596px"><div class="avatar" role="img" aria-label="Portrait of Marc Antell"></div><h4>Marc Antell</h4><p>Team Leader</p></div>
<div class="abs member" style="left:515px;top:596px"><div class="avatar" role="img" aria-label="Portrait of Joan Shore"></div><h4>Joan Shore</h4><p>Audit &amp; Accounts Team</p></div>

<h2 class="abs sec-title" style="left:124px;top:762px"><b></b>NEWS</h2>
<h2 class="abs sec-title" style="left:344px;top:762px"><b></b>BLOG</h2>
<h2 class="abs sec-title" style="left:520px;top:760px;width:116px"><b></b>UPCOMING EVENTS</h2>

<div class="abs news-item" style="top:800px"><div class="abs date">23<small>JUL</small></div><div class="abs news-text"><h5>searchable version</h5><p>A fully searchable A-Z version of the City Herald style guide that is designed to be used for all output</p></div></div>
<div class="abs rule" style="top:849px"></div>
<div class="abs news-item" style="top:863px"><div class="abs date">23<small>JUL</small></div><div class="abs news-text"><h5>searchable version</h5><p>A fully searchable A-Z version of the City Herald style guide that is designed to be used for all output</p></div></div>
<div class="abs rule" style="top:912px"></div>
<div class="abs news-item" style="top:925px"><div class="abs date">23<small>JUL</small></div><div class="abs news-text"><h5>searchable version</h5><p>A fully searchable A-Z version of the City Herald style guide that is designed to be used for all output</p></div></div>

<div class="abs blog-img" style="top:798px;background:linear-gradient(#2f6a1a,#7cc23a)" role="img" aria-label="Soccer ball resting on green grass"></div>
<p class="abs blog-cap" style="top:854px">Lorem ipsum dolor sit amet, consectetuer adipiscing elit, sed diam nonummy dolore magna aliquam erat volutpat.</p>
<div class="abs blog-img" style="top:885px;background:radial-gradient(circle at 40% 50%,#f0a030,#c03018 45%,#101018 80%)" role="img" aria-label="Soccer ball wrapped in fire"></div>
<p class="abs blog-cap" style="top:940px">Lorem ipsum dolor sit amet, consectetuer adipiscing elit, sed diam nonummy dolore magna aliquam erat volutpat.</p>

<aside class="abs events">
  <h3>PROPOSED DATES</h3>
  <p>Trivia Night<br>9th August<br>Junior Presentation day &amp;<br>AGM<br>11th October<br>Senior Presentation day<br>17th October</p>
</aside>

<section class="abs partners">
  <h3>WE DONATE TO</h3>
  <div class="partner-list"><span>Orvela</span><span>Northfield</span><span>Plainway</span><span>Harborline</span><span>Kestrel</span></div>
</section>

<div class="abs stripe"></div>
<footer class="abs footer">
  <div class="abs foot-brand"><i></i>BRIGHT NET RALLY</div>
  <div class="abs socials"><i></i><i></i><i></i><i></i><span>© 2014 - All Rights Reserved</span></div>
  <p class="abs foot-text">It is a long established fact that a reader will be distracted by the readable content of a page when looking at its layout. The point of using Lorem Ipsum is that it has a more-or-less normal distribution of letters, as opposed to using 'Content here, content here', making it look like readable English. Many desktop publishing packages and web page editors now use Lorem Ipsum as</p>
  <div class="abs foot-col" style="left:538px"><h4>Infomation</h4>Home<br>About club<br>Our team<br>Contacts<br>Blog</div>
  <div class="abs foot-col" style="left:626px"><h4>Support</h4>Terms of Service<br>Security<br>Privacy Policy<br>Sitemap<br>FAQ</div>
</footer>

</body>
</html>
```